Verodex business card

Business card for sustainable investment company called "Verodex". Verodex is an exchange platform selling carbon credits between buyers and sellers. Carbon Credits are an environmental commodity for reducing global carbon emissions.

the card should obviously have our logo and the theme should be sustainability/environment mixed with a trading platform.

Contact Information for Business Card

Logo, Name, Title, Phone, Email

Colors
0054AA
0677BA
7BADD7
CADEEF
E8F1F8
0094D4
00A9DD
6FCCEA
C7EBF8
E9F6FB
00AB8E
00BBA5
67D7C9
C6EFE9
E9F9F6
59FF00
82FF00
B8FF75
E3FFCB
F4FFEA

```html
<!DOCTYPE html>
<html lang="en">
<head>
<meta charset="utf-8">
<title>Verodex Business Card</title>
<link href="https://fonts.googleapis.com/css2?family=Montserrat:wght@600&family=Raleway:wght@500;800&display=swap" rel="stylesheet">
<style>
  :root {
    --backdrop: #e9f6fb;
    --navy: #0054aa;
    --ocean: #0677ba;
    --sky: #0094d4;
    --teal: #00ab8e;
    --teal-bright: #00bba5;
    --lime: #82ff00;
    --mint-wash: #e9f9f6;
    --ice: #f4fffa;
    --white: #ffffff;
  }
  * { margin: 0; padding: 0; box-sizing: border-box; }
  html, body { width: 1200px; height: 851px; overflow: hidden; }
  body {
    background: var(--backdrop);
    display: flex;
    flex-direction: column;
    align-items: center;
    justify-content: center;
    gap: 44px;
  }
  .card {
    width: 560px;
    height: 320px;
    border-radius: 22px;
    box-shadow: 0 12px 28px rgba(0, 84, 170, 0.22);
    position: relative;
    overflow: hidden;
  }
  .card-front {
    background: linear-gradient(135deg, var(--navy) 0%, var(--sky) 55%, var(--teal) 100%);
    color: var(--white);
    display: flex;
    align-items: center;
    justify-content: center;
  }
  .card-back {
    background: linear-gradient(135deg, var(--white) 0%, var(--mint-wash) 100%);
    color: var(--navy);
  }
  .accent-band {
    position: absolute;
    left: 0; right: 0; bottom: 0;
    height: 10px;
    background: linear-gradient(90deg, var(--navy), var(--sky) 40%, var(--teal-bright) 75%, var(--lime));
  }
  .brand {
    display: flex;
    align-items: center;
    gap: 18px;
    font-family: "Montserrat", sans-serif;
    font-weight: 600;
    letter-spacing: 1px;
  }
  .brand-mark { flex: none; border-radius: 50%; }
  .card-front .brand { font-size: 52px; }
  .card-front .brand-mark { width: 46px; height: 46px; background: var(--lime); }
  .card-back .brand {
    position: absolute;
    left: 42px;
    top: 180px;
    font-size: 30px;
    gap: 12px;
  }
  .card-back .brand-mark { width: 28px; height: 28px; background: var(--teal); }
  .contact {
    position: absolute;
    left: 300px;
    top: 76px;
    font-family: "Raleway", sans-serif;
  }
  .contact-name {
    font-weight: 800;
    font-size: 26px;
    letter-spacing: 0.5px;
    line-height: 1.1;
    color: var(--navy);
  }
  .contact-title {
    font-weight: 500;
    font-size: 17px;
    color: var(--teal);
    margin-bottom: 18px;
  }
  .contact-list { list-style: none; }
  .contact-list li {
    display: flex;
    align-items: center;
    gap: 10px;
    font-weight: 500;
    font-size: 15px;
    margin-bottom: 8px;
    color: var(--ocean);
  }
  .contact-list svg { width: 14px; height: 14px; flex: none; }
</style>
</head>
<body>
  <section class="card card-front">
    <div class="brand"><span class="brand-mark"></span><span class="brand-name">VERODEX</span></div>
  </section>

  <section class="card card-back">
    <div class="brand"><span class="brand-mark"></span><span class="brand-name">VERODEX</span></div>
    <div class="contact">
      <p class="contact-name">MARCUS HALE</p>
      <p class="contact-title">Founder &amp; CEO</p>
      <ul class="contact-list">
        <li>
          <svg viewBox="0 0 16 16" aria-hidden="true"><path fill="#00ab8e" d="M3.5 1.5l2.5 0 1 3.5-1.6 1.2c.8 1.7 2.2 3.1 3.9 3.9L10.5 8.5 14 9.5v2.5c0 1-1 2-2 2C6.5 14 2 9.5 2 4c0-1 .6-2.5 1.5-2.5z"/></svg>
          (555) 018-2746
        </li>
        <li>
          <svg viewBox="0 0 16 16" aria-hidden="true"><rect x="1" y="3" width="14" height="10" rx="1" fill="#00ab8e"/><path d="M1.5 4l6.5 5 6.5-5" fill="none" stroke="#ffffff" stroke-width="1.3"/></svg>
          office@verodex.com
        </li>
        <li>
          <svg viewBox="0 0 16 16" aria-hidden="true"><circle cx="8" cy="8" r="7" fill="#00ab8e"/><ellipse cx="8" cy="8" rx="3" ry="6.5" fill="none" stroke="#ffffff" stroke-width="1"/><path d="M1.5 8h13" stroke="#ffffff" stroke-width="1"/></svg>
          verodex.com
        </li>
      </ul>
    </div>
    <div class="accent-band"></div>
  </section>
</body>
</html>
```